Business Card design for law firm = Brightvale Australia

We are seeking a new design for our business cards.
We are keeping our logo, which is attached.
We need space for
Name
Title
Address is , which is
Level 7
214 Marlowe Street
Sydney NSW 2047
Phone :
Mobile :
Fax :
Email :
DX :
website www.brightvale-example.com.au

Industry/Entity Type

Law Firm / Banking and Finance

Contact Information for Business Card

We are seeking a new design for our business cards. We are keeping our logo. We need space for Name Title Address is Level 7 214 Marlowe Street Sydney NSW 2047 Phone Mobile Fax Email DX website www.brightvale-example.com.au

Colors
0054AA
0677BA
7BADD7
CADEEF
E8F1F8

Requirements
Must have
• see our website for general feel www.brightvale-example.com.au

```html
<!DOCTYPE html>
<html lang="en">
<head>
<meta charset="utf-8">
<title>Brightvale Australia – Business Card</title>
<link rel="stylesheet" href="https://fonts.googleapis.com/css2?family=EB+Garamond:wght@400&family=PT+Sans:wght@400;700&display=swap">
<style>
  :root {
    --backdrop: #2a2422;
    --card: #1b1b1d;
    --blue: #0677ba;
    --blue-light: #0fa3dc;
    --blue-deep: #0054aa;
    --text: #f2f2f2;
  }
  * { box-sizing: border-box; margin: 0; padding: 0; }
  html, body { width: 1200px; height: 842px; overflow: hidden; }
  body {
    background: var(--backdrop);
    position: relative;
    font-family: "PT Sans", sans-serif;
  }
  .card {
    position: absolute;
    top: 262px;
    width: 520px;
    height: 317px;
    background: var(--card);
    overflow: hidden;
    box-shadow: 0 10px 30px rgba(0,0,0,.5);
  }
  .card--contact { left: 50px; }
  .card--brand { left: 630px; }

  /* contact side */
  .band { position: absolute; left: 0; right: 0; height: 12px; background: var(--blue); }
  .band--top { top: 0; }
  .band--bottom { bottom: 0; }
  .contact {
    position: absolute;
    inset: 12px 0;
    display: flex;
    flex-direction: column;
    align-items: center;
    justify-content: center;
    text-align: center;
    color: var(--text);
  }
  .person-name {
    font-family: "EB Garamond", serif;
    font-size: 30px;
    color: var(--blue);
    line-height: 1;
  }
  .person-title { font-size: 14px; margin-top: 4px; }
  .divider { width: 80px; height: 1px; background: var(--blue-light); margin: 12px 0; }
  .address { font-size: 13.5px; }
  .details { font-size: 13.5px; line-height: 1.45; }
  .label { color: var(--blue); font-weight: 700; }

  /* brand side */
  .tab { position: absolute; width: 36px; background: var(--blue); }
  .tab::after {
    content: "";
    position: absolute;
    top: 0; bottom: 0;
    width: 3px;
    background: var(--blue-light);
  }
  .tab--left { left: 0; top: 150px; height: 92px; }
  .tab--left::after { right: -9px; }
  .tab--right { right: 0; top: 60px; height: 92px; }
  .tab--right::after { left: -9px; }
  .brand {
    position: absolute;
    left: 0; right: 0; top: 0; bottom: 0;
    display: flex;
    align-items: center;
    justify-content: center;
  }
  .brand-name {
    font-family: "PT Sans", sans-serif;
    font-weight: 400;
    font-size: 44px;
    color: var(--blue);
    line-height: 1;
  }
</style>
</head>
<body>
  <section class="card card--contact">
    <div class="band band--top"></div>
    <div class="contact">
      <p class="person-name">Daniel Hartley</p>
      <p class="person-title">Managing Director</p>
      <div class="divider"></div>
      <p class="address">Level 7, 214 Marlowe Street, Sydney NSW 2047</p>
      <div class="divider"></div>
      <p class="details"><span class="label">P:</span> 044-555 010 321 | <span class="label">M:</span> 044-555 010 321 | <span class="label">F:</span> 044-555 010 321</p>
      <p class="details"><span class="label">E:</span> info@brightvale-example.com | <span class="label">DX:</span> 0000555010321</p>
    </div>
    <div class="band band--bottom"></div>
  </section>

  <section class="card card--brand">
    <div class="tab tab--right"></div>
    <div class="tab tab--left"></div>
    <div class="brand">
      <p class="brand-name">Brightvale</p>
    </div>
  </section>
</body>
</html>
```